Business card design Needed for new logo / Construction business, home extensions and new builds

We need a business card design using our new logo files which i will attach to this project :)

We are a small construction business specialising in home extensions, new builds and property development. We are very ambitious and would appreciate professional and elegant designs for our new business card.

Very serious about using the services on MakerQuarry and recently acquired our new logo from here :)

Please get involved, i will feedback when i can as i am very busy but can respond daily, thanks

Target Market(s)

People that want to build onto their houses, new building developments or adding too their existing property

Industry/Entity Type

Construction

Contact Information for Business Card

Renwick Tolliver Construction, Lionel Ashby (Managing Director), Tel 07822254961, email - info@renwick-tolliver, www.renwick-tolliver.co.uk

Colors

Designer to choose colors to be used in the design.

Requirements
Must have
• I like a deep grey on the back please. A lot of you have provided black from and back, try mixing things up a little. The black looks cool 😎 Thanks

```html
<!DOCTYPE html>
<html lang="en">
<head>
<meta charset="utf-8">
<title>Renwick Tolliver Construction – Business Card</title>
<link rel="stylesheet" href="https://fonts.googleapis.com/css2?family=Open+Sans:wght@400;600;700&display=swap">
<style>
  :root {
    --backdrop: #16161a;
    --card-grey: #707274;
    --card-grey-ink: #55575a;
    --card-black: #1f1f24;
    --gold: #eaa823;
    --silver: #c9cacc;
    --white: #f4f4f4;
    --rule: #8a8a8e;
  }
  * { box-sizing: border-box; margin: 0; padding: 0; }
  html, body {
    width: 1200px; height: 780px; overflow: hidden;
    background: var(--backdrop);
    font-family: "Open Sans", Arial, sans-serif;
  }
  .canvas {
    width: 1200px; height: 780px;
    display: flex; align-items: center; justify-content: center; gap: 30px;
  }
  .card {
    width: 560px; height: 320px;
    border-radius: 22px;
    border: 3px solid var(--gold);
    position: relative;
    overflow: hidden;
    flex: none;
  }
  /* Front: deep grey with company name */
  .card--front {
    background: var(--card-grey);
    display: flex; align-items: center; justify-content: center;
  }
  .brand {
    display: flex; align-items: center; gap: 16px;
    color: var(--card-grey-ink);
    font-weight: 700;
  }
  .brand__mark {
    width: 46px; height: 46px;
    background: var(--card-grey-ink);
    flex: none;
  }
  .brand__name {
    font-size: 26px; line-height: 1.15; letter-spacing: 1px;
    text-transform: uppercase;
  }
  /* Back: black with contact details */
  .card--back {
    background: var(--card-black);
    color: var(--white);
  }
  .person {
    position: absolute; left: 36px; top: 120px;
    width: 226px;
  }
  .person__name {
    font-size: 32px; font-weight: 700; line-height: 1.1;
    white-space: nowrap;
  }
  .person__first { color: var(--silver); }
  .person__last { color: var(--gold); }
  .person__role {
    font-size: 16px; font-weight: 600; margin-top: 4px; padding-left: 2px;
  }
  .divider {
    position: absolute; left: 280px; top: 60px;
    width: 1px; height: 130px;
    background: var(--rule);
  }
  .contacts {
    position: absolute; left: 300px; top: 72px;
    list-style: none;
    font-size: 14px; line-height: 1;
  }
  .contacts li {
    display: flex; align-items: center; gap: 10px;
    margin-bottom: 16px;
    white-space: nowrap;
  }
  .contacts svg { width: 15px; height: 15px; flex: none; }
  .address {
    position: absolute; left: 36px; bottom: 52px;
    font-size: 16px; font-weight: 400;
  }
</style>
</head>
<body>
<main class="canvas">
  <section class="card card--front" aria-label="Card front">
    <div class="brand">
      <span class="brand__mark"></span>
      <span class="brand__name">Renwick Tolliver<br>Construction</span>
    </div>
  </section>

  <section class="card card--back" aria-label="Card back">
    <div class="person">
      <p class="person__name"><span class="person__first">Lionel</span> <span class="person__last">Ashby</span></p>
      <p class="person__role">Managing Director</p>
    </div>
    <span class="divider"></span>
    <ul class="contacts">
      <li>
        <svg viewBox="0 0 16 16" aria-hidden="true"><path fill="var(--gold)" d="M3.6 1.2l2.3 2.6-1.2 1.6c.9 2 2.5 3.6 4.5 4.6l1.6-1.2 2.6 2.3-1.3 2.3C7 13.6 2.4 9 1.4 3z"/></svg>
        <span>0782 225 4961</span>
      </li>
      <li>
        <svg viewBox="0 0 16 16" aria-hidden="true"><rect x="1" y="3" width="14" height="10" rx="1.5" fill="var(--gold)"/><path d="M1.8 4l6.2 5 6.2-5" fill="none" stroke="var(--card-black)" stroke-width="1.3"/></svg>
        <span>info@renwick-tolliver.co.uk</span>
      </li>
      <li>
        <svg viewBox="0 0 16 16" aria-hidden="true"><circle cx="8" cy="8" r="6.5" fill="none" stroke="var(--gold)" stroke-width="1.5"/><path d="M1.5 8h13M8 1.5c-3 3.5-3 9.5 0 13M8 1.5c3 3.5 3 9.5 0 13" fill="none" stroke="var(--gold)" stroke-width="1.2"/></svg>
        <span>www.renwick-tolliver.co.uk</span>
      </li>
    </ul>
    <p class="address">Fennick Lane, Holloway Vale, HV2 7QL</p>
  </section>
</main>
</body>
</html>
```